R. Talmont Realty, Inc business card (2 sided), letterhead (1 sided) & #10 envelope (1 sided)

business card of standard size utilizing the attached logo. Side one with logo, Owen Talmont (my name), President / Broker (title), 805-317-2684 (phone), www.rtalmontrealty.example (website), 1726 Harlow Avenue, Suite 4052 San Luis Obiso, CA 93628 (business address) owen.rtalmontrealty@mailbox.example (e-mail address),
Side two - Log

Letterhead and #10 envelope in the same theme
Updates

Project Deadline Extended
Reason: I think a 2 day deadline may be a bit ambitious on my part. I have extended the deadline to 4 days. Thanks!

Industry/Entity Type

Business

```html
<!DOCTYPE html>
<html lang="en">
<head>
<meta charset="utf-8">
<title>R. Talmont Realty, Inc — Business Card</title>
<link rel="stylesheet" href="https://fonts.googleapis.com/css2?family=Noto+Serif:wght@400;700&family=Open+Sans:wght@400;600&display=swap">
<style>
  :root {
    --page-bg: #e9e6e1;
    --card-white: #ffffff;
    --card-dark: #3b3b3d;
    --brand-blue: #1d6a91;
    --band-deep: #0d4a68;
    --band-light: #2b86b0;
    --ink: #333335;
    --rule: #6d6d6d;
    --on-dark: #f2f2f2;
  }
  * { box-sizing: border-box; margin: 0; padding: 0; }
  html, body { width: 1200px; height: 1184px; overflow: hidden; }
  body {
    position: relative;
    background: var(--page-bg);
    font-family: "Open Sans", Arial, sans-serif;
    color: var(--ink);
  }
  .card {
    position: absolute;
    width: 914px;
    height: 521px;
    box-shadow: 0 2px 6px rgba(0,0,0,.18);
  }
  .card--front { left: 243px; top: 41px; background: var(--card-white); }
  .card--back { left: 61px; top: 611px; background: var(--card-dark); }

  .brand-name {
    position: absolute;
    font-family: "Noto Serif", Georgia, serif;
    font-weight: 400;
    white-space: nowrap;
    display: flex;
    align-items: center;
    gap: 14px;
  }
  .brand-mark { display: block; width: 18px; height: 18px; }
  .card--front .brand-name {
    left: 62px; top: 208px;
    font-size: 31px;
    color: var(--brand-blue);
  }
  .card--front .brand-mark { background: var(--brand-blue); }
  .card--back .brand-name {
    left: 0; right: 0; top: 196px;
    justify-content: center;
    font-size: 50px;
    color: var(--on-dark);
  }
  .card--back .brand-mark { width: 26px; height: 26px; background: var(--on-dark); }

  .divider {
    position: absolute;
    left: 522px; top: 130px;
    width: 2px; height: 250px;
    background: #8a8a8a;
  }
  .contact { position: absolute; left: 552px; top: 140px; }
  .contact__name {
    font-family: "Noto Serif", Georgia, serif;
    font-weight: 700;
    font-size: 35px;
    color: var(--brand-blue);
    line-height: 1.1;
  }
  .contact__title {
    font-family: "Noto Serif", Georgia, serif;
    font-size: 27px;
    margin-top: 8px;
    line-height: 1.2;
  }
  .contact__list { list-style: none; margin-top: 26px; }
  .contact__item {
    display: flex; align-items: center; gap: 8px;
    font-size: 19px;
    line-height: 1;
    margin-bottom: 20px;
  }
  .contact__item--email { font-size: 17px; }
  .contact__icon { width: 16px; height: 16px; flex: none; }

  .footer-rule {
    position: absolute; left: 0; right: 0; top: 449px;
    height: 2px; background: var(--ink);
  }
  .footer-band {
    position: absolute; left: 0; right: 0; bottom: 0;
    height: 61px;
    background: linear-gradient(90deg, var(--band-deep) 0%, var(--band-light) 50%, var(--band-deep) 100%);
    display: flex; align-items: center; justify-content: center;
  }
  .website {
    font-family: "Open Sans", Arial, sans-serif;
    font-size: 27px;
    letter-spacing: 3.5px;
  }
  .footer-band .website { color: #ffffff; }
  .card--back .website {
    position: absolute; left: 0; right: 0; top: 430px;
    text-align: center;
    color: var(--on-dark);
  }
</style>
</head>
<body>
  <section class="card card--front" aria-label="Business card front">
    <div class="brand-name"><span class="brand-mark"></span>R. Talmont Realty, Inc</div>
    <div class="divider"></div>
    <div class="contact">
      <p class="contact__name">Owen Talmont</p>
      <p class="contact__title">President / Broker</p>
      <ul class="contact__list">
        <li class="contact__item">
          <svg class="contact__icon" viewBox="0 0 16 16" aria-hidden="true">
            <circle cx="8" cy="8" r="7" fill="none" stroke="#1d6a91" stroke-width="1.4"/>
            <path d="M5.5 4.5l1.5 0 .6 2-1 .8c.5 1 1.2 1.7 2.1 2.1l.8-1 2 .6v1.5c-3.5 0-6-2.5-6-6z" fill="#1d6a91"/>
          </svg>
          805-317-2684
        </li>
        <li class="contact__item contact__item--email">
          <svg class="contact__icon" viewBox="0 0 16 16" aria-hidden="true">
            <rect x="1" y="3.5" width="14" height="9" rx="1.5" fill="#1d6a91"/>
            <path d="M1.8 4.5L8 9l6.2-4.5" fill="none" stroke="#ffffff" stroke-width="1.2"/>
          </svg>
          owen.rtalmontrealty@mailbox.example
        </li>
      </ul>
    </div>
    <div class="footer-rule"></div>
    <div class="footer-band"><span class="website">www.rtalmontrealty.example</span></div>
  </section>

  <section class="card card--back" aria-label="Business card back">
    <div class="brand-name"><span class="brand-mark"></span>R. Talmont Realty, Inc</div>
    <p class="website">www.rtalmontrealty.example</p>
  </section>
</body>
</html>
```